Business Card Design for company

We want new business cards. We'd like something different-- yet still highly professional. Our tagline is Providing leadership, delivering success. Stock photos are ok, as long as they are relevant and look upscale.

Target Market(s)

Architecture/Business Management Consulting/Engineering Consulting

Contact Information for Business Card

dark gray background with pops of blue might be good, but you tell me. You're the designers. Rounded corners might be nice, but again, you tell me.

Font styles to use
Serif
Sans Serif

Colors
3276b5
5c5c5c
9d9d9d
fbfbfb

Requirements
Nice to have
• Something different, but still very professional.

```html
<!DOCTYPE html>
<html lang="en">
<head>
<meta charset="utf-8">
<title>Norvale International – Business Card</title>
<link rel="stylesheet" href="https://fonts.googleapis.com/css2?family=Montserrat:wght@400;500;600&family=Work+Sans:wght@400;500&display=swap">
<style>
  :root {
    --blue: #3276b5;
    --blue-bright: #3d7fd6;
    --grey-dark: #5c5c5c;
    --grey-light: #9d9d9d;
    --white: #fbfbfb;
    --card: #161616;
    --card-edge: #0d0d0d;
    --stage: #d9d9d9;
  }
  * { box-sizing: border-box; margin: 0; padding: 0; }
  html, body { width: 1200px; height: 890px; overflow: hidden; }
  body {
    background: var(--stage);
    font-family: "Work Sans", Arial, sans-serif;
    color: var(--white);
    position: relative;
  }
  .card {
    position: absolute;
    left: 300px;
    width: 600px;
    height: 360px;
    border-radius: 22px;
    overflow: hidden;
    background: linear-gradient(135deg, #1c1c1c 0%, var(--card) 55%, var(--card-edge) 100%);
    box-shadow: 0 10px 30px rgba(0,0,0,.25);
  }
  .card--back { top: 50px; }
  .card--front { top: 480px; }

  .brand { text-align: center; }
  .brand__name {
    font-family: "Montserrat", Arial, sans-serif;
    font-weight: 600;
    color: var(--white);
    letter-spacing: 0.12em;
    line-height: 1.15;
  }
  .brand__tagline {
    font-family: "Montserrat", Arial, sans-serif;
    font-weight: 500;
    color: var(--white);
    letter-spacing: 0.16em;
    text-transform: uppercase;
  }

  .card--back .brand {
    position: absolute;
    left: 0; right: 0; top: 118px;
  }
  .card--back .brand__name { font-size: 38px; }
  .card--back .brand__tagline { font-size: 11.5px; margin-top: 22px; }

  .card--front .brand {
    position: absolute;
    left: 36px; top: 88px; width: 250px;
  }
  .card--front .brand__name { font-size: 25px; }

  .divider {
    position: absolute;
    left: 306px; top: 48px;
    width: 1px; height: 180px;
    background: var(--blue);
  }

  .contact {
    position: absolute;
    left: 330px; top: 62px;
  }
  .contact__name {
    font-family: "Montserrat", Arial, sans-serif;
    font-weight: 600;
    font-size: 21px;
    letter-spacing: 0.06em;
    color: var(--blue-bright);
    text-transform: uppercase;
  }
  .contact__role {
    font-size: 15px;
    font-weight: 500;
    margin-top: 4px;
    letter-spacing: 0.03em;
  }
  .contact__list { list-style: none; margin-top: 18px; }
  .contact__item {
    display: flex;
    align-items: center;
    gap: 9px;
    font-size: 13.5px;
    line-height: 22px;
    letter-spacing: 0.02em;
  }
  .contact__icon { width: 11px; height: 11px; flex: none; }

  .address-band {
    position: absolute;
    left: 0; right: 0; bottom: 0;
    height: 62px;
    background: var(--blue);
    display: flex;
    align-items: center;
    padding-left: 40px;
    font-size: 16px;
    letter-spacing: 0.02em;
  }
  .address-band__rule {
    position: absolute;
    left: 0; right: 0; bottom: 70px;
    height: 2px;
    background: var(--blue-bright);
  }
</style>
</head>
<body>

  <section class="card card--back" aria-label="Card back">
    <div class="brand">
      <p class="brand__name">NORVALE<br>INTERNATIONAL</p>
      <p class="brand__tagline">Guiding strategy | Building lasting results</p>
    </div>
  </section>

  <section class="card card--front" aria-label="Card front">
    <div class="brand">
      <p class="brand__name">NORVALE<br>INTERNATIONAL</p>
    </div>

    <div class="divider"></div>

    <div class="contact">
      <p class="contact__name">Evan Calder</p>
      <p class="contact__role">Design Consultant</p>
      <ul class="contact__list">
        <li class="contact__item">
          <svg class="contact__icon" viewBox="0 0 12 12" aria-hidden="true"><path d="M3 1 L5 3.5 L4 5 Q5.5 7 7 8 L8.5 7 L11 9 L9.5 11 Q5 10.5 1 3 Z" fill="var(--blue-bright)"/></svg>
          +1 555-014-2270
        </li>
        <li class="contact__item">
          <svg class="contact__icon" viewBox="0 0 12 12" aria-hidden="true"><rect x="1" y="2.5" width="10" height="7" rx="1" fill="none" stroke="var(--blue-bright)" stroke-width="1.3"/><path d="M1.5 3 L6 6.5 L10.5 3" fill="none" stroke="var(--blue-bright)" stroke-width="1.3"/></svg>
          STUDIO@NORVALEINTL.COM
        </li>
        <li class="contact__item">
          <svg class="contact__icon" viewBox="0 0 12 12" aria-hidden="true"><rect x="1" y="2.5" width="10" height="7" rx="1" fill="none" stroke="var(--blue-bright)" stroke-width="1.3"/><path d="M1.5 3 L6 6.5 L10.5 3" fill="none" stroke="var(--blue-bright)" stroke-width="1.3"/></svg>
          HELLO@NORVALEINTL.COM
        </li>
        <li class="contact__item">
          <svg class="contact__icon" viewBox="0 0 12 12" aria-hidden="true"><circle cx="6" cy="6" r="5" fill="none" stroke="var(--blue-bright)" stroke-width="1.2"/><ellipse cx="6" cy="6" rx="2.2" ry="5" fill="none" stroke="var(--blue-bright)" stroke-width="1"/><path d="M1 6 H11" stroke="var(--blue-bright)" stroke-width="1"/></svg>
          www.norvaleintl.com
        </li>
      </ul>
    </div>

    <div class="address-band__rule"></div>
    <div class="address-band">4180 Harbor Crest Dr Tampa, Florida</div>
  </section>

</body>
</html>
```